Walk Beside The River

Business Card design

Target Market(s)

People who require support in the commnity

Industry/Entity Type

Mental Health Support

Contact Information for Business Card

Mental Health Support Rosalind Tavener walkbesidetheriver@mailcove.com.au 0481 637 092 PO Box 926 Ferncliff QLD 4590

Colors
6B429C
8869AF
B7A5CE
E3DAEB
F3F0F8

Requirements
Must have
• Logo & details listed above
Should not have
• No red or orange

```html
<!DOCTYPE html>
<html lang="en">
<head>
<meta charset="utf-8">
<title>Walk Beside The River – Business Card</title>
<link rel="stylesheet" href="https://fonts.googleapis.com/css2?family=Open+Sans:wght@400;600&display=swap">
<style>
  :root {
    --backdrop: #141414;
    --card: #fdfdf2;
    --purple: #6b429c;
    --sun: #eee632;
    --ink: #111111;
  }
  * { box-sizing: border-box; margin: 0; padding: 0; }
  html, body { width: 1200px; height: 780px; overflow: hidden; }
  body {
    background: var(--backdrop);
    font-family: "Open Sans", Arial, sans-serif;
    color: var(--ink);
    position: relative;
  }
  .card {
    position: absolute;
    top: 240px;
    width: 525px;
    height: 300px;
    background: var(--card);
    overflow: hidden;
  }
  .card--details { left: 60px; }
  .card--front { left: 615px; }

  .sun-disc {
    position: absolute;
    top: 50%;
    width: 190px;
    height: 190px;
    margin-top: -95px;
    border-radius: 50%;
    background: var(--sun);
  }
  .card--details .sun-disc { right: -95px; }
  .card--front .sun-disc { left: -95px; }

  .brand {
    position: absolute;
    display: flex;
    align-items: center;
    gap: 12px;
  }
  .brand__dot {
    width: 58px;
    height: 58px;
    border-radius: 50%;
    background: var(--purple);
    flex: none;
  }
  .brand__name {
    font-weight: 600;
    font-size: 17px;
    line-height: 1.2;
    color: var(--purple);
    width: 120px;
  }
  .card--details .brand { left: 34px; top: 30px; }
  .card--front .brand { right: 40px; top: 40px; }

  .details {
    position: absolute;
    left: 34px;
    bottom: 28px;
    font-size: 14.5px;
    line-height: 1.35;
  }
  .details__role, .details__name { display: block; }
  .details__name { margin-bottom: 6px; }
  .details__list { list-style: none; }
  .details__item { display: flex; align-items: center; gap: 8px; }
  .details__icon { width: 13px; height: 13px; flex: none; }
</style>
</head>
<body>
  <section class="card card--details">
    <div class="sun-disc"></div>
    <div class="brand">
      <span class="brand__dot"></span>
      <span class="brand__name">Walk Beside The River</span>
    </div>
    <div class="details">
      <span class="details__role">Mental Health Support</span>
      <span class="details__name">Rosalind Tavener</span>
      <ul class="details__list">
        <li class="details__item">
          <svg class="details__icon" viewBox="0 0 16 16" aria-hidden="true"><path d="M3 1h3l1.5 4-2 1.2a9 9 0 0 0 4.3 4.3L11 8.5l4 1.5v3a2 2 0 0 1-2 2A12 12 0 0 1 1 3a2 2 0 0 1 2-2z" fill="#eee632"/></svg>
          0481 637 092
        </li>
        <li class="details__item">
          <svg class="details__icon" viewBox="0 0 16 16" aria-hidden="true"><rect x="1" y="3" width="14" height="10" rx="1.5" fill="#eee632"/><path d="M1.5 4l6.5 5 6.5-5" stroke="#fdfdf2" stroke-width="1.3" fill="none"/></svg>
          walkbesidetheriver@mailcove.com.au
        </li>
        <li class="details__item">
          <svg class="details__icon" viewBox="0 0 16 16" aria-hidden="true"><path d="M8 1a5 5 0 0 1 5 5c0 4-5 9-5 9S3 10 3 6a5 5 0 0 1 5-5z" fill="#eee632"/><circle cx="8" cy="6" r="1.8" fill="#fdfdf2"/></svg>
          PO Box 926 Ferncliff QLD 4590
        </li>
      </ul>
    </div>
  </section>

  <section class="card card--front">
    <div class="sun-disc"></div>
    <div class="brand">
      <span class="brand__dot"></span>
      <span class="brand__name">Walk Beside The River</span>
    </div>
  </section>
</body>
</html>
```